Fleyer für Rasenroboter-Garage
Zielgruppe
Aluminiumsysteme
Aufgabenstellung
Für ein neues Produkt " Rasenroboter-Garage" einen Fleyer entwerfen. Format DinA4 Vorder und Rückseite. Bilder der Garage sind als Anhang anbei.Es gibt eine Basic Version mit Dach und eine Expert Version mit Dach und Seitenverkleidung. Sogan " Das Zuhause für Ihren Rasenroboter" . Merkmale sind hochertige Materialien, qualitative Verarbeitung, ästhetisches Design,lange Lebensdauer.

```html
<!DOCTYPE html>
<html lang="de">
<head>
<meta charset="utf-8">
<title>GARDOBOX – Flyer Rasenroboter-Garage</title>
<link rel="stylesheet" href="https://fonts.googleapis.com/css2?family=Exo+2:wght@400;600;700&display=swap">
<style>
  :root {
    --stage: #ffffff;
    --ink: #0b0b0b;
    --white: #ffffff;
    --green-deep: #3f9a1c;
    --green-mid: #6dbb2e;
    --green-light: #c8ec8a;
    --logo-green: #7cc425;
    --badge-fill: #f4fbe2;
    --badge-line: #8cc63f;
    --badge-text: #6aa81e;
    --garage: #2f5a45;
  }
  * { margin: 0; padding: 0; box-sizing: border-box; }
  html, body { width: 1200px; height: 675px; overflow: hidden; background: var(--stage); }
  body { position: relative; font-family: "Exo 2", sans-serif; }

  .page {
    position: absolute; top: 8px; width: 427px; height: 602px; overflow: hidden;
    background: radial-gradient(ellipse 80% 55% at 55% 48%, var(--green-light) 0%, var(--green-mid) 45%, var(--green-deep) 100%);
  }
  .page--front { left: 110px; }
  .page--back { left: 626px; }

  .header {
    position: absolute; left: 0; top: 0; width: 100%; height: 146px;
    background: var(--ink); border-bottom-left-radius: 30px 26px;
  }
  .brand {
    position: absolute; left: 64px; top: 28px; display: flex; align-items: center; gap: 12px;
  }
  .brand__mark { width: 26px; height: 26px; background: var(--logo-green); }
  .brand__name {
    font-weight: 700; font-size: 50px; letter-spacing: 2px; color: var(--logo-green); line-height: 1;
  }
  .slogan {
    position: absolute; left: 20px; top: 114px; color: var(--white);
    font-size: 17px; font-weight: 600; letter-spacing: 0.6px;
  }

  .badge { position: absolute; }
  .badge svg { position: absolute; inset: 0; width: 100%; height: 100%; }
  .badge__label {
    position: absolute; inset: 0; display: flex; align-items: center; justify-content: center;
    text-align: center; color: var(--badge-text); font-size: 18px; line-height: 1.15; font-weight: 400;
  }
  .badge--expert { left: 35px; top: 170px; width: 104px; height: 102px; }
  .badge--basic { left: 300px; top: 84px; width: 102px; height: 104px; }

  .photo { position: absolute; }
  .photo--garage { background: linear-gradient(160deg, #3d6e56 0%, var(--garage) 55%, #1d3a2c 100%); }
  .photo--robot { background: linear-gradient(160deg, #456f5a 0%, #2f5a45 50%, #b8403a 100%); }
  .photo--grass {
    left: 0; width: 100%;
    background: linear-gradient(180deg, rgba(120,190,60,0) 0%, #5fa82a 35%, #3a7d1a 100%);
  }

  .copy { position: absolute; color: var(--white); font-size: 10px; line-height: 1.2; }
  .copy__title { display: inline-block; padding-bottom: 3px; margin-bottom: 5px; border-bottom: 1px solid var(--white); }

  .footer {
    position: absolute; left: 0; bottom: 0; width: 100%; height: 62px; background: var(--ink);
    color: var(--white); font-size: 10px;
  }
  .footer::before {
    content: ""; position: absolute; left: 0; right: 0; top: -8px; height: 14px;
    background: var(--ink); border-top: 2px solid #b7d83a; border-radius: 50% 50% 0 0 / 100% 100% 0 0;
  }
  .features { position: absolute; left: 40px; top: 14px; }
  .features__list {
    margin-top: 9px; display: grid; grid-template-columns: 175px 150px; list-style: none; line-height: 1.15;
  }
  .features__list li::before { content: "•"; margin-right: 8px; }
  .address { position: absolute; left: 38px; top: 14px; line-height: 1.2; }
</style>
</head>
<body>

<section class="page page--front">
  <header class="header">
    <div class="brand">
      <span class="brand__mark"></span>
      <span class="brand__name">GARDOBOX</span>
    </div>
    <p class="slogan">Das Zuhause für Ihren Rasenroboter</p>
  </header>

  <div class="photo photo--grass" style="top:362px;height:185px" role="img" aria-label="Foto: Grashalme im Gegenlicht"></div>

  <div class="badge badge--expert">
    <svg viewBox="0 0 100 100" aria-hidden="true">
      <polygon points="30,3 70,3 97,30 97,70 70,97 30,97 3,70 3,30" fill="var(--badge-fill)" stroke="var(--badge-line)" stroke-width="3"/>
      <polygon points="32,9 68,9 91,32 91,68 68,91 32,91 9,68 9,32" fill="none" stroke="var(--badge-line)" stroke-width="1"/>
    </svg>
    <span class="badge__label">Expert<br>Version</span>
  </div>

  <div class="photo photo--garage" style="left:192px;top:176px;width:235px;height:208px" role="img" aria-label="Foto: Garage mit Dach und Seitenverkleidung, darin ein Rasenroboter"></div>
  <div class="photo photo--garage" style="left:34px;top:362px;width:122px;height:86px" role="img" aria-label="Foto: Garage Expert Version mit Rasenroboter, Seitenansicht"></div>

  <div class="copy" style="left:38px;top:292px">
    <span class="copy__title">Version 1:</span><br>
    Diese Version hat ein<br>Dach sowie eine<br>Seitenverkleidung.
  </div>

  <footer class="footer">
    <div class="features">
      Merkmale:
      <ul class="features__list">
        <li>Hochertige Material</li>
        <li>Ästhetisches Design</li>
        <li>Qualitative Verarbeitung</li>
        <li>Lange Lebensdauer</li>
      </ul>
    </div>
  </footer>
</section>

<section class="page page--back">
  <div class="photo photo--grass" style="top:365px;height:185px" role="img" aria-label="Foto: Grashalme im Gegenlicht"></div>

  <div class="photo photo--robot" style="left:16px;top:68px;width:280px;height:150px" role="img" aria-label="Foto: Garage Basic Version mit Dach, darunter ein Rasenroboter"></div>

  <div class="badge badge--basic">
    <svg viewBox="0 0 100 100" aria-hidden="true">
      <polygon points="30,3 70,3 97,30 97,70 70,97 30,97 3,70 3,30" fill="var(--badge-fill)" stroke="var(--badge-line)" stroke-width="3"/>
      <polygon points="32,9 68,9 91,32 91,68 68,91 32,91 9,68 9,32" fill="none" stroke="var(--badge-line)" stroke-width="1"/>
    </svg>
    <span class="badge__label">Basic<br>Version</span>
  </div>

  <div class="copy" style="left:39px;top:248px">
    <span class="copy__title">Version 2:</span><br>
    Diese Version hat ein<br>Dach aber keine<br>Seitenverkleidung.
  </div>

  <div class="photo photo--robot" style="left:244px;top:260px;width:137px;height:80px" role="img" aria-label="Foto: Basic Version, Seitenansicht mit Rasenroboter"></div>
  <div class="photo photo--robot" style="left:38px;top:308px;width:100px;height:92px" role="img" aria-label="Foto: Basic Version, Frontansicht mit Rasenroboter"></div>

  <footer class="footer">
    <p class="address">Hier könnte Ihre Anschrift ect.<br>stehen</p>
  </footer>
</section>

</body>
</html>
```